MRT Property - Business Cards

Looking for a business card & general letterhead, signage etc design for our new logo.

Colours:
000a20
0056a2
00b5ef
0088ce
68cef2

Fonts:
Poppins
Karla

Please keep look and feel of new brand - example in the zip package I sent.

```html
<!DOCTYPE html>
<html lang="en">
<head>
<meta charset="utf-8">
<title>MRT Property – Business Card</title>
<link rel="stylesheet" href="https://fonts.googleapis.com/css2?family=Montserrat:wght@400;500&family=Neucha&family=Poppins:wght@700&display=swap">
<style>
  :root {
    --backdrop: #9b9b9b;
    --navy: #121527;
    --brand-blue: #0a57a5;
    --accent: #1a8fd1;
    --light-blue: #68cef2;
    --white: #ffffff;
  }
  * { margin: 0; padding: 0; box-sizing: border-box; }
  html, body {
    width: 1093px; height: 1200px; overflow: hidden;
    background: var(--backdrop);
    font-family: "Montserrat", Arial, sans-serif;
  }
  .card {
    position: absolute; left: 265px; width: 580px;
    border-radius: 22px; overflow: hidden;
  }
  .card-front { top: 225px; height: 362px; background: var(--navy); color: var(--white); }
  .card-back { top: 616px; height: 366px; background: var(--brand-blue); }

  .wordmark {
    font-family: "Poppins", Arial, sans-serif; font-weight: 700;
    color: var(--white); white-space: nowrap; line-height: 1;
    display: flex; align-items: center;
  }
  .front-wordmark { position: absolute; left: 27px; top: 58px; font-size: 31px; }
  .back-wordmark {
    position: absolute; left: 0; right: 0; top: 155px;
    justify-content: center; font-size: 54px; gap: 18px;
  }
  .wordmark-dot {
    width: 34px; height: 34px; border-radius: 50%;
    background: var(--light-blue); flex: none;
  }

  .holder { position: absolute; right: 32px; top: 22px; text-align: right; }
  .holder-name {
    font-family: "Neucha", cursive; font-size: 29px; color: var(--accent);
    line-height: 1.1;
  }
  .holder-title { font-size: 13.5px; font-weight: 400; letter-spacing: .3px; margin-top: 1px; }
  .holder-bar {
    position: absolute; right: 0; top: 27px; width: 14px; height: 41px;
    background: var(--brand-blue);
  }

  .address {
    position: absolute; left: 31px; top: 197px;
    font-size: 14px; line-height: 16px;
  }
  .contacts {
    position: absolute; left: 31px; top: 270px;
    list-style: none; font-size: 13.5px; letter-spacing: .2px;
  }
  .contacts li { display: flex; align-items: center; height: 24.5px; }
  .contacts svg { width: 13px; height: 13px; margin-right: 9px; fill: var(--accent); flex: none; }
  .bottom-band {
    position: absolute; left: 0; right: 0; bottom: 0; height: 15px;
    background: var(--brand-blue);
  }
</style>
</head>
<body>
  <section class="card card-front">
    <div class="wordmark front-wordmark">MRT Property</div>

    <div class="holder">
      <p class="holder-name">Dana Whitlow</p>
      <p class="holder-title">Managing Director</p>
    </div>
    <div class="holder-bar"></div>

    <address class="address" style="font-style:normal">
      42 Cedar Ridge Lane<br>
      Hartwell, MS 39000
    </address>

    <ul class="contacts">
      <li>
        <svg viewBox="0 0 24 24" aria-hidden="true"><path d="M6.6 10.8a15.1 15.1 0 0 0 6.6 6.6l2.2-2.2a1 1 0 0 1 1-.25 11.4 11.4 0 0 0 3.6.57 1 1 0 0 1 1 1V20a1 1 0 0 1-1 1A17 17 0 0 1 3 4a1 1 0 0 1 1-1h3.5a1 1 0 0 1 1 1c0 1.25.2 2.45.57 3.57a1 1 0 0 1-.25 1z"/></svg>
        555.204.7713
      </li>
      <li>
        <svg viewBox="0 0 24 24" aria-hidden="true"><path d="M2 5h20v2l-10 6L2 7z"/><path d="M2 9l10 6 10-6v10H2z"/></svg>
        info@mrtproperty.com
      </li>
      <li>
        <svg viewBox="0 0 24 24" aria-hidden="true"><circle cx="12" cy="12" r="10"/><path d="M2 12h20M12 2c3 3 3 17 0 20M12 2c-3 3-3 17 0 20" stroke="#121527" stroke-width="1.6" fill="none"/></svg>
        www.mrtproperty.com
      </li>
    </ul>

    <div class="bottom-band"></div>
  </section>

  <section class="card card-back">
    <div class="wordmark back-wordmark">
      <span class="wordmark-dot"></span>
      MRT Property
    </div>
  </section>
</body>
</html>
```